Presentation Folder with inside Pockets

We need a Presentation Folder with inside pockets. The size of the folder will be 9" x 12" and will be printed on the cover, the back and the inside folder flaps. The design will be very simple and consist of our logo (large) on the front cover and our logo (smaller) and contact information on the back. We are open to various colors that you think may go along with our logo. When you display your work, show the front, back and inside.

Target Market(s)

Pharmaceutical Companies

Industry/Entity Type

Work

Requirements
Should not have
• please do not add stock medical photos.

```html
<!DOCTYPE html>
<html lang="en">
<head>
<meta charset="utf-8">
<title>Meridian Trials Inc. — Presentation Folder</title>
<link href="https://fonts.googleapis.com/css2?family=Open+Sans:wght@400;600;700;800&display=swap" rel="stylesheet">
<style>
  :root {
    --stage: #000000;
    --blue-light: #1e97d6;
    --blue-dark: #124a72;
    --paper: #ffffff;
    --ink: #111111;
    --pocket-grey: #e2e2e2;
    --green-dark: #5e9440;
    --green-light: #9cc93a;
    --accent-orange: #f08a1c;
    --muted: #444444;
  }
  * { margin: 0; padding: 0; box-sizing: border-box; }
  html, body { width: 1200px; height: 1008px; overflow: hidden; background: var(--stage); }
  body { position: relative; font-family: "Open Sans", Arial, sans-serif; }

  .back-cover {
    position: absolute; left: 96px; top: 59px; width: 509px; height: 679px;
    background: linear-gradient(to bottom, var(--blue-light) 0%, var(--blue-dark) 100%);
    color: var(--paper); text-align: center;
  }
  .back-cover .mark {
    position: absolute; left: 50%; top: 445px; transform: translateX(-50%);
    width: 96px; height: 96px; border-radius: 50%; background: var(--paper);
  }
  .back-cover .brand {
    position: absolute; left: 0; right: 0; top: 556px;
    font-weight: 800; font-size: 28px; letter-spacing: 1px; line-height: 1.05;
  }
  .back-cover .brand small { display: block; font-size: 20px; }
  .back-cover .contact {
    position: absolute; left: 0; right: 0; top: 621px;
    font-size: 12.5px; line-height: 22px;
  }
  .contact .icon { display: inline-block; vertical-align: -2px; margin: 0 3px 0 8px; }

  .front-cover {
    position: absolute; left: 605px; top: 59px; width: 510px; height: 648px;
    background: var(--paper);
  }
  .front-cover .logo-lockup {
    position: absolute; left: 42px; top: 31px; display: flex; align-items: center; gap: 16px;
  }
  .front-cover .mark {
    width: 76px; height: 76px; border-radius: 50%; background: var(--accent-orange);
  }
  .front-cover .brand {
    font-weight: 800; font-size: 28px; letter-spacing: 1px; line-height: 1.05; color: var(--ink); text-align: center;
  }
  .front-cover .brand small { display: block; font-size: 20px; }

  .web-band {
    position: absolute; left: 605px; top: 707px; width: 510px; height: 31px;
    background: linear-gradient(to right, var(--blue-dark) 0%, var(--blue-light) 30%, var(--blue-light) 100%);
    color: var(--paper); font-size: 13px; letter-spacing: 2px; text-align: center; line-height: 31px;
  }
  .web-band strong { font-weight: 700; }

  .pockets { position: absolute; left: 0; top: 0; }

  .business-card {
    position: absolute; width: 199px; height: 116px; background: var(--paper);
    border: 1px solid #bbbbbb; color: var(--ink); font-size: 5.5px; line-height: 8px;
  }
  .business-card .card-brand {
    position: absolute; left: 10px; top: 12px; display: flex; align-items: center; gap: 5px;
    font-weight: 800; font-size: 8.5px; letter-spacing: .3px;
  }
  .business-card .card-brand i {
    width: 18px; height: 18px; border-radius: 50%; background: var(--accent-orange); display: block;
  }
  .business-card .card-contact { position: absolute; left: 12px; top: 68px; color: var(--muted); }
  .business-card .card-address { position: absolute; left: 12px; top: 92px; color: var(--muted); }
  .business-card .card-person { position: absolute; right: 24px; top: 68px; text-align: center; font-weight: 600; }
  .card-left { left: 229px; top: 782px; }
  .card-right { left: 780px; top: 800px; }
</style>
</head>
<body>

  <section class="back-cover">
    <div class="mark"></div>
    <div class="brand">MERIDIAN TRIALS<small>INC.</small></div>
    <div class="contact">
      <div>
        <svg class="icon" width="11" height="11" viewBox="0 0 12 12"><path d="M3 1 L5 3.5 L4 5 Q5.5 7 7 8 L8.5 7 L11 9 L9.5 11 Q4 10 1 3 Z" fill="#fff"/></svg>+1-555-014-2290
        <svg class="icon" width="12" height="10" viewBox="0 0 12 10"><rect x="0.5" y="0.5" width="11" height="9" rx="1" fill="#fff"/><path d="M1 1 L6 5.5 L11 1" stroke="#124a72" fill="none"/></svg>hello@meridiantrials.net
      </div>
      <div>Meridian Trials Inc. 52 Linden Avenue, Fairview, NY 10990</div>
    </div>
  </section>

  <section class="front-cover">
    <div class="logo-lockup">
      <div class="mark"></div>
      <div class="brand">MERIDIAN TRIALS<small>INC.</small></div>
    </div>
  </section>

  <div class="web-band">www.<strong>meridiantrials</strong>.net</div>

  <svg class="pockets" width="1200" height="1008" viewBox="0 0 1200 1008">
    <defs>
      <linearGradient id="pocketGreen" x1="0" y1="0" x2="0" y2="1">
        <stop offset="0" stop-color="#5e9440"/>
        <stop offset="1" stop-color="#9cc93a"/>
      </linearGradient>
    </defs>
    <polygon class="pocket-left" points="96,738 605,738 537,951 96,951" fill="#e2e2e2"/>
    <polygon class="pocket-right" points="608,738 1115,738 1115,951 676,951" fill="url(#pocketGreen)"/>
    <g class="crop-marks" stroke="#cccccc" stroke-width="1">
      <line x1="222" y1="775" x2="238" y2="791"/><line x1="420" y1="775" x2="436" y2="791"/>
      <line x1="222" y1="905" x2="238" y2="889"/><line x1="420" y1="905" x2="436" y2="889"/>
      <line x1="773" y1="793" x2="789" y2="809"/><line x1="968" y1="793" x2="984" y2="809"/>
      <line x1="773" y1="921" x2="789" y2="905"/><line x1="968" y1="921" x2="984" y2="905"/>
    </g>
  </svg>

  <div class="business-card card-left">
    <div class="card-brand"><i></i>MERIDIAN TRIALS INC.</div>
    <div class="card-contact">+1-555-014-2290<br>hello@meridiantrials.net</div>
    <div class="card-person">Your Name<br>Title</div>
    <div class="card-address">Meridian Trials Inc. 52 Linden Avenue<br>Fairview, NY 10990</div>
  </div>

  <div class="business-card card-right">
    <div class="card-brand"><i></i>MERIDIAN TRIALS INC.</div>
    <div class="card-contact">+1-555-014-2290<br>hello@meridiantrials.net</div>
    <div class="card-person">Your Name<br>Title</div>
    <div class="card-address">Meridian Trials Inc. 52 Linden Avenue<br>Fairview, NY 10990</div>
  </div>

</body>
</html>
```